Irrigation Business needs their business cards modernised and revamped

I would like to keep my current logo, colours and revamp the format of the card.

I would like the card to be clean yet important.

Im not sure if you include texture but i would like the named logo to be indented into the card etc.

show me something alive and free something thats clinical to the point yet has a feel of achievement. i would like people to go nice card.

Target Market(s)

high end clients, corporate, sports field manger, the guys that make the decisions

Industry/Entity Type

Business

Contact Information for Business Card

nformation to be included

Dean Harlow (Director)
0487305526
dean@kolvat.biz
www.kestonfieldworks.com

instagram logo
google logo
facebook logo

Colors

Designer to choose colors to be used in the design.

Requirements
Nice to have
• indentations a really nice feel to the card good texture

```html
<!DOCTYPE html>
<html lang="en">
<head>
<meta charset="utf-8">
<title>Keston Fieldworks – Business Card</title>
<link href="https://fonts.googleapis.com/css2?family=Roboto:wght@700&family=Questrial&family=Roboto+Condensed:wght@700&display=swap" rel="stylesheet">
<style>
  :root{
    --bg:#1c1c1d;
    --card:#f2f2f1;
    --navy:#0f4a92;
    --sky:#1ea3dc;
    --green:#1e8a3c;
    --ink:#2b2b2b;
    --ghost:#e2e2e2;
  }
  html,body{margin:0;padding:0;width:1200px;height:1001px;overflow:hidden;background:var(--bg);}
  .stage{position:relative;width:1200px;height:1001px;}
  .card{position:absolute;left:308px;width:584px;height:318px;border-radius:24px;background:var(--card);overflow:hidden;}
  .card--front{top:140px;}
  .card--back{top:542px;}

  .front-ghost{position:absolute;left:308px;top:-4px;width:304px;height:304px;border-radius:50%;background:var(--ghost);}
  .front-mark{position:absolute;left:111px;top:30px;width:72px;height:72px;border-radius:50%;background:var(--navy);}
  .brand{position:absolute;margin:0;font-family:"Roboto",Arial,sans-serif;font-weight:700;color:var(--navy);letter-spacing:-0.3px;white-space:nowrap;}
  .brand--front{left:46px;top:110px;font-size:21px;}
  .contact-name{position:absolute;left:46px;top:200px;margin:0;font-family:"Roboto Condensed",Arial,sans-serif;font-size:15px;color:var(--navy);}
  .contact-name .role{font-family:"Questrial",sans-serif;font-weight:400;color:var(--green);margin-left:6px;}
  .contact-list{position:absolute;left:46px;top:226px;margin:0;padding:0;list-style:none;font-family:"Questrial",sans-serif;font-size:13.5px;line-height:18.5px;color:var(--ink);}

  .back-art{position:absolute;left:-140px;top:-60px;width:400px;height:400px;border-radius:50%;background:linear-gradient(180deg,var(--sky) 0%,#1378bf 55%,var(--navy) 100%);}
  .brand--back{right:36px;top:64px;font-size:25px;}
  .social{position:absolute;left:430px;top:217px;display:flex;gap:8px;}
  .social span{width:34px;height:34px;border-radius:5px;background:var(--navy);}
  .back-url{position:absolute;right:36px;top:262px;margin:0;font-family:"Questrial",sans-serif;font-size:14px;color:var(--ink);}
</style>
</head>
<body>
<main class="stage">
  <section class="card card--front">
    <div class="front-ghost" aria-hidden="true"></div>
    <div class="front-mark" aria-hidden="true"></div>
    <h1 class="brand brand--front">KESTON FIELDWORKS</h1>
    <p class="contact-name">DEAN HARLOW <span class="role">/ &nbsp;DIRECTOR</span></p>
    <ul class="contact-list">
      <li>0487305526</li>
      <li>dean@kolvat.biz</li>
      <li>www.kestonfieldworks.com</li>
    </ul>
  </section>

  <section class="card card--back">
    <div class="back-art" role="img" aria-label="Large blue brand graphic area"></div>
    <h2 class="brand brand--back">KESTON FIELDWORKS</h2>
    <div class="social" aria-label="Social media links"><span></span><span></span><span></span></div>
    <p class="back-url">www.kestonfieldworks.com</p>
  </section>
</main>
</body>
</html>
```